Financial Advisor Resource Firm needs business card design

Need business card design for company in Omaha NE called Meridale Circle. We provide resources to financial advisors....workshop programs, retirement analysis, and insurance planning. I would like to see designs that use grays, greens, black, and white colors. The final design should communicate 'collaboration' and be simple yet attractive to financial planning clients. I will attached our logo and another picture of a puzzle piece coming together. I would like the incorporate the puzzle picture somehow, maybe on the back somehow, with color or just the gray scale....OR, the picture be the front of the card with 'Meridale' definition on it (see upload) and then company logo, employee name, title, address on the back (see ppt uploaded). The following disclosure needs to be included somewhere- Advisory services offered through Stonebrook Assets, LLC.
Updates

I uploaded a svg and ai file of the logo

Target Market(s)

Financial planning clients and financial advisors....so pretty diverse age range of about 40-70.

Industry/Entity Type

Financial Planning

Contact Information for Business Card

Tobias L. Fenwright, MBA
Founder/President
5287 E. Larkin Road
Suite 230
Omaha, NE 68190
Phone- (402) 555-0147
Cell- (402) 555-0183
Fax- (402) 555-0129
email- tobias@meridaleplan.example
web address- www.meridaleplan.example

Colors
1b1b1b
474747
d3d3d3
ffffff
9bcb3c
abd036

Requirements
Must have
• Must include logo provided, must be 2 sided, and must have disclosure...all of these items listed in project description

```html
<!DOCTYPE html>
<html lang="en">
<head>
<meta charset="utf-8">
<title>Meridale Circle – Business Card</title>
<link rel="stylesheet" href="https://fonts.googleapis.com/css2?family=Poppins:wght@400;500;600&display=swap">
<style>
  :root {
    --ink: #1b1b1b;
    --charcoal: #2b2b2b;
    --slate: #474747;
    --mist: #d3d3d3;
    --paper: #ffffff;
    --leaf: #9bcb3c;
    --lime: #abd036;
    --stage: #ecebe8;
  }
  * { box-sizing: border-box; margin: 0; padding: 0; }
  html, body {
    width: 1200px;
    height: 920px;
    overflow: hidden;
  }
  body {
    background: var(--stage);
    font-family: "Poppins", sans-serif;
    position: relative;
  }
  .card {
    position: absolute;
    top: 315px;
    width: 534px;
    height: 300px;
    overflow: hidden;
    box-shadow: 0 6px 18px rgba(0,0,0,0.18);
  }
  .card--front { left: 52px; background: var(--paper); }
  .card--back  { left: 620px; background: var(--charcoal); }

  .brand {
    display: flex;
    align-items: center;
    gap: 8px;
    font-weight: 500;
    letter-spacing: 1px;
    text-transform: uppercase;
    white-space: nowrap;
  }
  .brand__dot {
    width: 12px;
    height: 12px;
    border-radius: 50%;
    background: var(--leaf);
    flex: none;
  }
  .card--front .brand {
    position: absolute;
    left: 24px;
    top: 135px;
    font-size: 17px;
    color: var(--ink);
  }
  .divider {
    position: absolute;
    left: 272px;
    top: 78px;
    width: 2px;
    height: 144px;
    background: var(--leaf);
  }
  .contact {
    position: absolute;
    left: 287px;
    top: 76px;
    color: var(--slate);
  }
  .contact__name {
    font-size: 16.5px;
    font-weight: 500;
    color: var(--leaf);
    letter-spacing: 0.3px;
    line-height: 1.3;
  }
  .contact__title {
    font-size: 11.5px;
    margin-top: 3px;
    margin-bottom: 12px;
  }
  .contact__list { list-style: none; }
  .contact__item {
    display: flex;
    align-items: center;
    gap: 9px;
    font-size: 12.5px;
    line-height: 18.5px;
  }
  .contact__icon { width: 10px; height: 10px; flex: none; }
  .accent { color: var(--leaf); }

  .swoosh {
    position: absolute;
    left: 0;
    bottom: 0;
    width: 534px;
    height: 70px;
  }

  .card--back .brand {
    position: absolute;
    left: 0;
    right: 0;
    top: 115px;
    justify-content: center;
    font-size: 26px;
    color: var(--paper);
  }
  .card--back .brand__dot { width: 16px; height: 16px; }
  .address {
    position: absolute;
    left: 0;
    right: 0;
    top: 206px;
    text-align: center;
    font-size: 11px;
    letter-spacing: 0.4px;
    color: var(--mist);
  }
  .web {
    position: absolute;
    left: 0;
    right: 0;
    top: 232px;
    text-align: center;
    font-size: 12px;
    letter-spacing: 1px;
    color: var(--paper);
  }
  .disclosure {
    position: absolute;
    left: 0;
    right: 0;
    top: 266px;
    text-align: center;
    font-size: 9.5px;
    letter-spacing: 0.3px;
    color: var(--mist);
    opacity: 0.8;
  }
</style>
</head>
<body>

<section class="card card--front" aria-label="Card front">
  <div class="brand"><span class="brand__dot"></span>Meridale Circle</div>
  <div class="divider"></div>

  <div class="contact">
    <p class="contact__name">TOBIAS L. FENWRIGHT, MBA</p>
    <p class="contact__title">Founder / President</p>
    <ul class="contact__list">
      <li class="contact__item">
        <svg class="contact__icon" viewBox="0 0 10 10"><path d="M2 0.5 L3.6 2.6 L2.7 3.6 Q3.8 6 6.4 7.3 L7.4 6.4 L9.5 8 L8.4 9.5 Q1 8 0.5 1.6 Z" fill="var(--leaf)"/></svg>
        (402) 555-0147
      </li>
      <li class="contact__item">
        <svg class="contact__icon" viewBox="0 0 10 10"><rect x="2.5" y="0.5" width="5" height="9" rx="1" fill="none" stroke="var(--leaf)" stroke-width="1.2"/><rect x="4.3" y="7.4" width="1.4" height="0.9" fill="var(--leaf)"/></svg>
        (402) 555-0183
      </li>
      <li class="contact__item">
        <svg class="contact__icon" viewBox="0 0 10 10"><rect x="2.5" y="0.5" width="5" height="3" fill="var(--leaf)"/><rect x="0.5" y="3.5" width="9" height="4" rx="0.8" fill="var(--leaf)"/><rect x="2.5" y="6.5" width="5" height="3" fill="none" stroke="var(--leaf)" stroke-width="1"/></svg>
        (402) 555-0129
      </li>
      <li class="contact__item">
        <svg class="contact__icon" viewBox="0 0 10 10"><rect x="0.5" y="2" width="9" height="6.5" fill="none" stroke="var(--leaf)" stroke-width="1"/><path d="M0.5 2 L5 5.8 L9.5 2" fill="none" stroke="var(--leaf)" stroke-width="1"/></svg>
        tobias@meridaleplan.example
      </li>
      <li class="contact__item">
        <svg class="contact__icon" viewBox="0 0 10 10"><circle cx="5" cy="5" r="4.4" fill="none" stroke="var(--leaf)" stroke-width="1"/><ellipse cx="5" cy="5" rx="1.9" ry="4.4" fill="none" stroke="var(--leaf)" stroke-width="0.9"/><line x1="0.6" y1="5" x2="9.4" y2="5" stroke="var(--leaf)" stroke-width="0.9"/></svg>
        <span>www.<span class="accent">meridaleplan</span>.example</span>
      </li>
    </ul>
  </div>

  <svg class="swoosh" viewBox="0 0 534 70" preserveAspectRatio="none" aria-hidden="true">
    <path d="M0 38 Q165 56 308 54 Q442 52 534 36 L534 70 L0 70 Z" fill="var(--charcoal)"/>
    <path d="M0 24 Q123 40 267 42 Q411 42 534 22 L534 27 Q411 48 267 48 Q123 48 0 34 Z" fill="var(--leaf)"/>
  </svg>
</section>

<section class="card card--back" aria-label="Card back">
  <div class="brand"><span class="brand__dot"></span>Meridale Circle</div>
  <p class="address">5287 E. Larkin Road, Suite 230 &nbsp;|&nbsp; Omaha, NE 68190</p>
  <p class="web">www.<span class="accent">meridaleplan</span>.example</p>
  <p class="disclosure">Advisory services offered through Stonebrook Assets, LLC.</p>
</section>

</body>
</html>
```